Banner Ad Designs for tick and flea products

We sell tick and flea products online and want some great banner designs for our online website to promote our tick and flea products.

The ads must be made up in both Flash and HTML5
Ads can be formatted as .JPEG or .GIF files.

Please see the following url for creative requirements
http://help.bannerkite.com/creative-requirements/

Creative licence no limits to your imagination!

Ads must be created in the following sizes:

- Banner – 468×60
- Square – 250×250
- Small Square – 200×200
- Leaderboard – 728×90
- Medium Rectangle – 300×250
- Chatterly – 100×72

please view our website at www.globalpawstore.com.au or .com to get a feel for our website.

The aim is to attract customers who want to save on tick and flea purchases for their pets (dogs and cats)

Target Market(s)

Anyone who owns a dog or cat

Industry/Entity Type

Online

Font styles to use
Sans Serif
Other font styles liked:
• creative licence on font styles

Requirements
Must have
• Must have a strong urge to entice customers to click through.

Images wording and text etc use creative lic
Nice to have
• Strong appeal to dog and cat owners and how they can save on flea and tick essentials.
Keep it simple but effective.
Be fun and playful and inviting.
Should not have
• Please do not use words like cheap - cheapest

Strobing & Flashing - Strobing, flashing backgrounds, or otherwise distracting ads are not allowed. Do not attempt to overtly distract the user from page content.

```html
<!DOCTYPE html>
<html lang="en">
<head>
<meta charset="utf-8">
<title>Global Paw Store – Small Square Banners</title>
<link rel="stylesheet" href="https://fonts.googleapis.com/css2?family=Tenor+Sans&family=Archivo:wght@800&display=swap">
<style>
  :root {
    --page-bg: #ffffff;
    --frame: #7cb13a;
    --green-light: #a8cc5a;
    --green-mid: #82b037;
    --green-deep: #5e8f26;
    --header-white: #ffffff;
    --brand-ink: #1f2f55;
    --copy-white: #ffffff;
    --button-top: #8af25a;
    --button-bottom: #1fae1a;
    --button-edge: #137a12;
    --button-ink: #123d10;
    --caption-ink: #111111;
    --photo-a: #c9b59a;
    --photo-b: #e9e4da;
  }
  * { box-sizing: border-box; margin: 0; padding: 0; }
  html, body { width: 1200px; height: 533px; overflow: hidden; background: var(--page-bg); }
  .canvas { position: relative; width: 1200px; height: 533px; }

  .banner {
    position: absolute;
    top: 133px;
    width: 240px;
    height: 240px;
    border: 3px solid var(--frame);
    overflow: hidden;
    background: linear-gradient(180deg, var(--green-light) 30%, var(--green-mid) 55%, var(--green-deep) 100%);
    font-family: "Tenor Sans", sans-serif;
    color: var(--copy-white);
  }
  .banner--copy { left: 235px; }
  .banner--photo { left: 492px; }
  .banner--cta { left: 749px; }

  .banner__header {
    position: absolute;
    left: -30%;
    top: -20px;
    width: 160%;
    height: 108px;
    background: var(--header-white);
    border-radius: 0 0 50% 50% / 0 0 38px 38px;
    box-shadow: 0 6px 14px rgba(255,255,255,0.85);
  }

  .brand {
    position: absolute;
    top: 24px;
    left: 0;
    width: 100%;
    display: flex;
    align-items: center;
    justify-content: center;
    gap: 8px;
    color: var(--brand-ink);
    font-family: "Tenor Sans", sans-serif;
    font-size: 19px;
  }
  .brand__dot {
    width: 30px;
    height: 30px;
    border-radius: 50%;
    background: var(--brand-ink);
  }

  .headline {
    position: absolute;
    left: 0;
    width: 100%;
    text-align: center;
    font-size: 24px;
    line-height: 29px;
    text-shadow: 0 1px 2px rgba(0,0,0,0.15);
  }
  .banner--copy .headline { top: 114px; }
  .banner--photo .headline { top: 124px; left: 118px; width: 116px; font-size: 23px; line-height: 28px; }
  .banner--cta .headline { top: 118px; }

  .pet-photo {
    position: absolute;
    left: 0;
    bottom: 0;
    width: 125px;
    height: 108px;
    background: radial-gradient(ellipse at 45% 55%, var(--photo-a) 0%, var(--photo-b) 75%, rgba(233,228,218,0) 100%);
  }

  .order-button {
    position: absolute;
    left: 22px;
    top: 168px;
    width: 196px;
    height: 54px;
    border: 2px solid var(--button-edge);
    border-radius: 8px;
    background: linear-gradient(180deg, var(--button-top) 0%, var(--button-top) 45%, var(--button-bottom) 55%, var(--button-bottom) 100%);
    display: flex;
    align-items: center;
    justify-content: center;
    font-family: "Archivo", sans-serif;
    font-weight: 800;
    font-size: 25px;
    letter-spacing: -0.5px;
    color: var(--button-ink);
  }

  .size-caption {
    position: absolute;
    top: 414px;
    left: 0;
    width: 1160px;
    text-align: center;
    font-family: "Tenor Sans", sans-serif;
    font-size: 26px;
    color: var(--caption-ink);
  }
</style>
</head>
<body>
<main class="canvas">
  <section class="banner banner--copy">
    <div class="banner__header"></div>
    <div class="brand"><span class="brand__dot"></span><span class="brand__name">Global Paw Store</span></div>
    <p class="headline">Save on<br>genuine brand<br>tick and flea<br>products</p>
  </section>

  <section class="banner banner--photo">
    <div class="banner__header"></div>
    <div class="brand"><span class="brand__dot"></span><span class="brand__name">Global Paw Store</span></div>
    <div class="pet-photo" role="img" aria-label="Photo of a small dog and a tabby cat lying together"></div>
    <p class="headline">Protect<br>Your<br>Pets!</p>
  </section>

  <section class="banner banner--cta">
    <div class="banner__header"></div>
    <div class="brand"><span class="brand__dot"></span><span class="brand__name">Global Paw Store</span></div>
    <p class="headline">Save with us</p>
    <div class="order-button">ORDER NOW</div>
  </section>

  <p class="size-caption">Small Square – 200×200</p>
</main>
</body>
</html>
```